Calm Nest

I currently have a squarespace website www.bodysensepillow.comI want a complete design change but I want you to use the current information on the site.
Updates

We will be making a decision this week. Thank You.

```html
<!DOCTYPE html>
<html lang="en">
<head>
<meta charset="utf-8">
<title>Calm Nest</title>
<link href="https://fonts.googleapis.com/css2?family=Lato:wght@300;400;700;900&display=swap" rel="stylesheet">
<style>
:root{
  --ink:#111111;
  --black:#000000;
  --white:#ffffff;
  --text:#555555;
  --muted:#8a8a8a;
  --rule:#333333;
  --line:#d6d6d6;
  --soft:#f0f0f0;
  --card:#dcdcdc;
  --footer:#161616;
  --footer-bottom:#0b0b0b;
}
*{box-sizing:border-box;margin:0;padding:0}
html,body{width:1200px;height:4418px;overflow:hidden}
body{position:relative;background:var(--white);font-family:'Lato',sans-serif;color:var(--ink)}
.abs{position:absolute}
.photo{position:absolute}

/* header + hero */
.hero{left:0;top:0;width:1200px;height:892px;overflow:hidden}
.hero-photo{left:0;top:0;width:1200px;height:892px;
  background:radial-gradient(ellipse at 50% 25%,#8f8f8f 0%,#5a5a5a 45%,#2e2e2e 100%)}
.hero-photo::after{content:"";position:absolute;left:0;top:330px;width:1200px;height:562px;
  background:radial-gradient(ellipse at 60% 60%,#e9e2dc 0%,#cfc6c4 35%,#8a7f7c 70%,rgba(60,60,60,0) 100%)}
.menu{left:160px;top:38px;width:32px}
.menu span{display:block;height:2px;background:var(--white);margin-bottom:8px}
.logo{font-family:'Lato',sans-serif;font-weight:400;letter-spacing:2px;display:flex;align-items:center;gap:10px;color:var(--white)}
.logo i{display:block;width:26px;height:26px;border:2px solid currentColor}
.hero .logo{left:440px;top:30px;font-size:38px}
.tools{right:160px;top:40px;display:flex;gap:16px}
.hero h1{left:0;width:1200px;top:178px;text-align:center;color:var(--white);font-weight:900;font-size:44px;line-height:54px;text-transform:uppercase}
.btn{display:inline-block;background:var(--black);color:var(--white);font-weight:700;text-align:center}
.hero-cta{left:518px;top:343px;width:164px;height:51px;line-height:51px;font-size:19px;border-radius:3px}
.discover{left:197px;top:732px;color:var(--white);font-size:16px}
.discover::after{content:"";position:absolute;left:14px;top:10px;width:132px;height:12px;background:var(--black);z-index:-1}
.slides{left:1022px;top:832px;display:flex}
.slides span{width:59px;height:60px;line-height:60px;text-align:center;font-weight:700;font-size:19px;color:var(--white);background:#2a2a2a}
.slides span:first-child{background:var(--black)}

/* section titles */
.title{font-weight:700;font-size:41px;line-height:48px;color:var(--ink)}
.title.center{left:0;width:1200px;text-align:center}
.rule{display:flex;align-items:center;gap:6px;height:4px;margin-top:12px}
.title.center .rule{justify-content:center}
.rule b{display:block;height:4px;background:var(--rule)}
.rule .l{width:51px}.rule .m{width:20px}
.rule em{display:block;width:4px;height:4px;background:var(--rule)}

/* about */
.about-title{left:163px;top:955px}
.about-lead{left:163px;top:1056px;width:400px;font-weight:700;font-size:12px;line-height:20px}
.about-body{left:163px;width:430px;font-size:11px;line-height:19px;color:var(--text)}
.btn.small{height:36px;line-height:36px;font-size:14px;border-radius:3px}
.about-btn{left:162px;top:1327px;width:112px}

/* cards */
.cards{left:160px;top:1563px;display:flex;gap:19px}
.card{width:206px;height:302px;background:var(--white);box-shadow:0 0 6px rgba(0,0,0,.25);text-align:center}
.card .pic{height:151px;background:linear-gradient(160deg,#e4e4e4,#cfcfcf)}
.card h3{font-size:13px;font-weight:700;margin:18px 0 6px}
.card p{font-size:11px;line-height:19px;color:var(--muted);padding:0 18px;height:60px}
.card a{font-size:11px;font-weight:700;color:var(--ink);text-decoration:none}

/* sheets */
.tabs{left:489px;top:2025px;display:flex;border:1px solid var(--ink)}
.tabs span{width:111px;height:42px;line-height:42px;text-align:center;font-size:14px;font-weight:700}
.tabs .on{background:var(--black);color:var(--white)}
.features-title{left:612px;top:2118px;font-size:18px;font-weight:700}
.features{left:612px;top:2193px;list-style:none}
.features li{position:relative;padding-left:38px;height:39px;font-size:11px;color:var(--muted);line-height:20px}
.features li::before{content:"";position:absolute;left:0;top:9px;width:14px;height:2px;background:#666}
.features li::after{content:"";position:absolute;left:12px;top:6px;width:8px;height:8px;border-radius:50%;background:#444}
.sheets-btn{left:611px;top:2479px;width:113px}

/* service band */
.band-text{left:163px;top:2642px;color:var(--white);font-weight:700;font-size:22px;line-height:30px}
.band-btn{left:162px;top:2722px;width:112px;height:36px;line-height:36px;background:var(--white);color:var(--ink);font-size:14px;border-radius:3px}

/* products */
.products-title{left:163px;top:2857px}
.prod-main{left:0;top:2978px;width:749px;height:411px;background:linear-gradient(120deg,#6e6560 0%,#8b7f76 45%,#a49588 100%)}
.prod-main::before{content:"";position:absolute;left:0;top:0;width:520px;height:411px;
  background:radial-gradient(ellipse at 0% 100%,rgba(60,55,55,.85),rgba(90,85,85,.2) 70%,rgba(0,0,0,0) 100%)}
.prod-top{left:749px;top:2978px;width:451px;height:222px;background:linear-gradient(160deg,#b9c3c8,#e9ecee 60%,#c9ced2)}
.prod-bottom{left:749px;top:3200px;width:451px;height:189px;background:linear-gradient(140deg,#5aaed2,#7fc3e0 50%,#4c9cc2)}
.prod-copy{left:163px;top:3190px;color:var(--white)}
.prod-copy h3{font-size:19px;line-height:28px;font-weight:400}
.prod-copy h3 b{font-weight:700}
.prod-copy p{font-size:11px;line-height:19px;width:290px;margin-top:10px}
.prod-btn{left:163px;top:3305px;width:111px}
.arrows{left:566px;top:3420px;display:flex;gap:3px}
.arrows span{width:32px;height:30px;border:1px solid var(--ink);display:flex;align-items:center;justify-content:center}
.arrows span:first-child{background:var(--black)}

/* contact */
.contact-title{top:3504px}
.field{border:1px solid #9a9a9a;font-size:11px;color:var(--muted);padding:12px 12px}
.submit{left:543px;top:3878px;width:112px;height:35px;line-height:35px;font-size:14px;border-radius:3px}

/* social */
.social{left:0;top:3974px;width:1200px;height:127px;background:var(--soft);text-align:center}
.social h4{font-weight:400;font-size:24px;margin-top:26px}
.social .dots{display:flex;justify-content:center;gap:36px;margin-top:14px}
.social .dots i{display:block;width:20px;height:20px;border-radius:50%;background:var(--ink)}

/* footer */
.footer{left:0;top:4101px;width:1200px;height:267px;background:var(--footer);color:var(--white)}
.footer .logo{position:absolute;left:163px;top:44px;font-size:26px}
.footer .logo i{width:20px;height:20px}
.f-col{position:absolute;top:56px;font-size:11px;line-height:24px}
.f-col h5{font-size:13px;font-weight:700;margin-bottom:12px}
.f-about{left:163px;top:94px;width:200px;font-size:11px;line-height:19px;position:absolute}
.f-contact p{display:flex;gap:14px;align-items:flex-start;margin-bottom:14px;line-height:18px}
.f-input{width:202px;height:28px;border:1px solid #9a9a9a;font-size:11px;padding:6px 8px;margin-top:14px}
.f-sub{width:202px;height:28px;line-height:28px;background:var(--white);color:var(--ink);font-weight:700;font-size:12px;text-align:center;margin-top:8px}
.bottom{left:0;top:4368px;width:1200px;height:50px;background:var(--footer-bottom);color:#cfcfcf;font-size:11px;text-align:center;line-height:50px}
.bottom b{color:var(--white)}
</style>
</head>
<body>

<header class="hero abs">
  <div class="photo hero-photo" role="img" aria-label="Child sleeping peacefully on a white pillow under a white duvet"></div>
  <div class="menu abs"><span></span><span></span><span></span></div>
  <div class="logo abs"><i></i>CALM NEST</div>
  <div class="tools abs">
    <svg width="18" height="18" viewBox="0 0 18 18" fill="none" stroke="#fff" stroke-width="1.6"><circle cx="7.5" cy="7.5" r="5.5"/><path d="M11.5 11.5l5 5"/></svg>
    <svg width="18" height="18" viewBox="0 0 18 18" fill="none" stroke="#fff" stroke-width="1.6"><circle cx="9" cy="6" r="4"/><path d="M1.5 17c1-4 4-5.5 7.5-5.5s6.5 1.5 7.5 5.5z"/></svg>
  </div>
  <h1 class="abs">Helping people sleep better is the<br>most important thing that we do.</h1>
  <a class="btn hero-cta abs">CONTACT US</a>
  <div class="discover abs">+ Discover More</div>
  <div class="slides abs"><span>01</span><span>02</span><span>03</span></div>
</header>

<section>
  <h2 class="title about-title abs">About Us<div class="rule"><b class="l"></b><b class="m"></b><em></em><em></em><b class="l"></b></div></h2>
  <p class="about-lead abs">Helping People Sleep Better Is The Most Important Thing That<br>We Do. Live Well, Sleep Well.</p>
  <p class="about-body abs" style="top:1114px">Calm Nest believes that sleep is the most important part of your life. We created Calm Nest because better sleep makes for a better life. We carry a variety of speciality sleep products that are made with the finest materials available.</p>
  <p class="about-body abs" style="top:1193px">We believe that having the correct pillow is essential to achieving the best night of sleep. Pillows play a vital role in supporting the intricate structures of the head, neck, shoulders, hips, and spine. Pillows can help alleviate or prevent many common forms of back and neck pain, as well as shoulder, hip and other forms of joint pain.</p>
  <a class="btn small about-btn abs">Read More</a>
  <svg class="abs" style="left:626px;top:896px" width="574" height="582" viewBox="0 0 574 582" role="img" aria-label="Smiling couple relaxing together on a bed">
    <defs><linearGradient id="aboutPhoto" x1="0" y1="0" x2="1" y2="1"><stop offset="0" stop-color="#b9a89a"/><stop offset=".45" stop-color="#e3dcd6"/><stop offset="1" stop-color="#6f6a69"/></linearGradient></defs>
    <path d="M60 132C122 52 196 70 246 100C320 142 352 30 452 14C524 4 574 44 574 60L574 574C498 590 418 572 346 532C256 482 148 572 78 514C16 462 38 390 10 312C-12 238 20 180 60 132Z" fill="#cfcfcf"/>
    <path d="M52 122C114 44 190 62 240 92C314 134 346 22 446 6C518-4 574 36 574 52L574 560C494 578 414 560 342 520C252 470 146 560 74 502C12 450 32 380 6 302C-16 228 14 170 52 122Z" fill="url(#aboutPhoto)"/>
  </svg>
</section>

<section>
  <h2 class="title center abs" style="top:1450px">Know More About Pillows<div class="rule"><b class="l"></b><b class="m"></b><em></em><em></em><b class="l"></b></div></h2>
  <div class="cards abs">
    <article class="card"><div class="pic" role="img" aria-label="Two light blue quilted pillows"></div><h3>ERGO CHILL</h3><p>Lorem Ipsum is simply dummy text of the printing and typesetting industry.</p><a>Read More →</a></article>
    <article class="card"><div class="pic" role="img" aria-label="Two cream latex pillows"></div><h3>PURE COMFORT</h3><p>Proprietary noodle latex foam mixed with super soft and cool gel fibers, both breathable and soft.</p><a>Read More →</a></article>
    <article class="card"><div class="pic" role="img" aria-label="White pillow with contrast edge piping"></div><h3>WARM BALANCE</h3><p>Warm Balance ensures calm sleep, even if your body temperature suddenly rises.</p><a>Read More →</a></article>
    <article class="card"><div class="pic" role="img" aria-label="Two natural cream pillows"></div><h3>EARTH REST</h3><p>Earth Rest provides you with a blend of Kapok and Latex that provides a natural night.</p><a>Read More →</a></article>
  </div>
</section>

<section>
  <h2 class="title center abs" style="top:1922px">Know More About Sheets<div class="rule"><b class="l"></b><b class="m"></b><em></em><em></em><b class="l"></b></div></h2>
  <svg class="abs" style="left:0;top:2006px" width="572" height="578" viewBox="0 0 572 578" role="img" aria-label="Bright bedroom with a bed made in white sheets">
    <defs><linearGradient id="sheetsPhoto" x1="0" y1="0" x2="1" y2="1"><stop offset="0" stop-color="#8c9078"/><stop offset=".4" stop-color="#f1f1ef"/><stop offset="1" stop-color="#a9a79c"/></linearGradient></defs>
    <path d="M0 36C84-4 164 46 234 96C304 146 334 46 424 86C546 136 568 268 536 368C506 466 466 508 386 518C286 528 264 578 182 566C100 552 40 528 0 508Z" fill="#cfcfcf"/>
    <path d="M0 30C80-10 160 40 230 90C300 140 330 40 420 80C540 130 560 260 530 360C500 460 460 500 380 510C280 520 260 572 180 558C100 545 40 520 0 500Z" fill="url(#sheetsPhoto)"/>
  </svg>
  <div class="tabs abs"><span>BAMBOO</span><span class="on">COOL</span></div>
  <h3 class="features-title abs">FEATURES :</h3>
  <ul class="features abs">
    <li>Controls The Micro-Climate Keeping The Body In.</li>
    <li>The 'Comfort Zone'.</li>
    <li>Enhances Thermal Comfort.</li>
    <li>Reduces Perspiration And No Effect On Fabric.</li>
    <li>Breathability.</li>
    <li>Quick Dry Technology.</li>
    <li>Eco-Friendly Product</li>
  </ul>
  <a class="btn small sheets-btn abs">Read More</a>
</section>

<section>
  <svg class="abs" style="left:0;top:2571px" width="1200" height="261" viewBox="0 0 1200 261">
    <defs><linearGradient id="bandPhoto" x1="0" y1="0" x2="1" y2="0"><stop offset="0" stop-color="#2c3a52"/><stop offset=".4" stop-color="#c7c2b8"/><stop offset="1" stop-color="#e6e1dc"/></linearGradient></defs>
    <path d="M549 38C640 10 700 0 800 0L1200 0L1200 261L640 261C600 261 570 240 549 228Z" fill="url(#bandPhoto)" role="img" aria-label="Woman resting against a cooling pillow on a bed"/>
    <path d="M0 38L700 38A95 95 0 0 1 700 228L0 228Z" fill="#000"/>
  </svg>
  <p class="band-text abs">We are available &nbsp;24/7 &nbsp;a week to our customers.<br>We take pride in our customer service.</p>
  <a class="btn band-btn abs">Contact Us</a>
</section>

<section>
  <h2 class="title products-title abs">Our 2019 Products<div class="rule"><b class="l"></b><b class="m"></b><em></em><em></em><b class="l"></b></div></h2>
  <div class="photo prod-main" role="img" aria-label="Smiling woman sitting in soft bedding"></div>
  <div class="photo prod-top" role="img" aria-label="Woman lying on a bed with white sheets"></div>
  <div class="photo prod-bottom" role="img" aria-label="Close-up of blue quilted pillow fabric"></div>
  <div class="prod-copy abs">
    <h3>2019 Amber<br><b>Willow ComfortBedding</b></h3>
    <p>We carry the highest quality pillows, sheets, blankets and mattress protectors in the industry.</p>
  </div>
  <a class="btn small prod-btn abs">Read More</a>
  <div class="arrows abs">
    <span><svg width="10" height="14" viewBox="0 0 10 14" fill="none" stroke="#fff" stroke-width="2.2"><path d="M8 1L2 7l6 6"/></svg></span>
    <span><svg width="10" height="14" viewBox="0 0 10 14" fill="none" stroke="#111" stroke-width="2.2"><path d="M2 1l6 6-6 6"/></svg></span>
  </div>
</section>

<section>
  <h2 class="title center contact-title abs">Contact Us<div class="rule"><b class="l"></b><b class="m"></b><em></em><em></em><b class="l"></b></div></h2>
  <div class="field abs" style="left:310px;top:3607px;width:278px;height:42px">Name:</div>
  <div class="field abs" style="left:610px;top:3607px;width:278px;height:42px">Email:</div>
  <div class="field abs" style="left:310px;top:3674px;width:278px;height:43px">Phone:</div>
  <div class="field abs" style="left:610px;top:3674px;width:278px;height:43px">Subject:</div>
  <div class="field abs" style="left:310px;top:3740px;width:578px;height:88px">Message:</div>
  <a class="btn submit abs">Submit</a>
</section>

<section class="social abs">
  <h4>Get Social With Us</h4>
  <div class="dots"><i></i><i></i><i></i><i></i><i></i></div>
</section>

<footer class="footer abs">
  <div class="logo"><i></i>CALM NEST</div>
  <p class="f-about">Calm Nest believes that sleep is the most important part of your life. We created Calm Nest because better sleep makes for a better life.</p>
  <div class="f-col" style="left:387px;top:52px">
    <h5>Useful Link</h5>
    About Us<br>2019 Products<br>Press<br>Why Become Retailer<br>Why Become Wholesale<br>Customer Service &amp; Support
  </div>
  <div class="f-col f-contact" style="left:612px;top:52px;width:200px">
    <h5>Contact Us</h5>
    <p><svg width="16" height="16" viewBox="0 0 16 16" fill="#fff"><path d="M3 1l3 3-2 2c1 2 3 4 6 6l2-2 3 3-2 2C7 15 1 9 1 3z"/></svg>+91-000-000-0000</p>
    <p><svg width="16" height="12" viewBox="0 0 16 12" fill="#fff"><path d="M0 0h16v12H0z"/><path d="M0 0l8 6 8-6" stroke="#161616" stroke-width="1.5" fill="none"/></svg>info@calmnest.example</p>
    <p><svg width="14" height="18" viewBox="0 0 14 18" fill="#fff"><path d="M7 0a7 7 0 0 0-7 7c0 5 7 11 7 11s7-6 7-11a7 7 0 0 0-7-7zm0 10a3 3 0 1 1 0-6 3 3 0 0 1 0 6z"/></svg>100- Lorem ipsum is simply<br>dummy text.</p>
  </div>
  <div class="f-col" style="left:837px;top:52px;width:210px">
    <h5>Newsletter</h5>
    <div style="line-height:13px;font-size:11px">You can get latest update from us by subscribing to our newsletter.</div>
    <div class="f-input">Enter Your Email:</div>
    <div class="f-sub">Subscribe Now!</div>
  </div>
</footer>
<div class="bottom abs">Copyright © 2019 <b>CALM NEST</b>. All Rights Reserved. | Terms &amp; Conditions.</div>

</body>
</html>
```